KTL Stewardship Powerpoint project

Hello, I would like a highly professional powerpoint design that uses the new logo that we had designed for my consulting company. I have created a starting point in powerpoint but the successful designer must take it to a new level. i would like to see a professional image on the front page as well as our website address on a banner at the bottom (www.ktlstewardship.com.au). It is going to be the document we use for presentations that will introduce my company so it must be special!

Industry/Entity Type

It Company

Requirements
Nice to have
• Some sort of design in the front page - attached is company logo for your use.

```html
<!DOCTYPE html>
<html lang="en">
<head>
<meta charset="utf-8">
<title>KTL Stewardship – Presentation Template</title>
<link href="https://fonts.googleapis.com/css2?family=Carlito:wght@400;700&display=swap" rel="stylesheet">
<style>
  :root {
    --stage: #e9edf2;
    --ink-dark: #141414;
    --header-grey: #4a4a4a;
    --body-white: #ffffff;
    --footer-light: #f4f4f4;
    --footer-mid: #dcdcdc;
    --brand-blue: #2a8ccf;
    --text-black: #111111;
    --text-white: #ffffff;
    --text-soft: #cfcfcf;
  }
  * { box-sizing: border-box; margin: 0; padding: 0; }
  html, body {
    width: 1200px;
    height: 638px;
    overflow: hidden;
    background: var(--stage);
    font-family: "Carlito", "Calibri", Arial, sans-serif;
  }
  .deck {
    display: flex;
    gap: 28px;
    justify-content: center;
    align-items: center;
    height: 100%;
  }
  .slide {
    position: relative;
    width: 560px;
    height: 420px;
    overflow: hidden;
    box-shadow: 0 4px 14px rgba(0, 0, 0, 0.25);
  }

  /* Cover slide */
  .slide--cover {
    background:
      radial-gradient(ellipse 55% 26% at 50% 45%, #ffffff 0%, #e6e6e6 35%, rgba(120,120,120,0.55) 70%, rgba(20,20,20,0) 100%),
      linear-gradient(180deg, #2a2a2a 0%, var(--ink-dark) 45%, #0c0c0c 100%);
  }
  .cover-band {
    position: absolute;
    left: 0; right: 0;
    top: 120px;
    height: 140px;
    background: linear-gradient(90deg, rgba(0,0,0,0) 0%, rgba(255,255,255,0.35) 30%, rgba(255,255,255,0.35) 70%, rgba(0,0,0,0) 100%);
  }
  .cover-brand {
    position: absolute;
    left: 0; right: 0;
    top: 170px;
    display: flex;
    justify-content: center;
    align-items: center;
    gap: 10px;
  }
  .brand-mark {
    width: 14px;
    height: 14px;
    background: var(--brand-blue);
  }
  .brand-name {
    color: var(--brand-blue);
    font-weight: 700;
    font-size: 30px;
    letter-spacing: 0.5px;
  }
  .cover-web {
    position: absolute;
    left: 0; right: 0;
    top: 334px;
    text-align: center;
    color: var(--text-soft);
    font-size: 10px;
    letter-spacing: 1px;
    text-transform: uppercase;
  }

  /* Content slide */
  .slide--content { background: var(--body-white); }
  .content-header {
    height: 70px;
    background: var(--header-grey);
    display: flex;
    align-items: center;
    padding-left: 34px;
  }
  .content-title {
    color: var(--text-white);
    font-size: 26px;
    font-weight: 400;
  }
  .content-body {
    padding: 10px 0 0 34px;
  }
  .content-body li {
    list-style: none;
    color: var(--text-black);
    font-size: 23px;
  }
  .content-body li::before {
    content: "•";
    margin-right: 12px;
  }
  .content-footer {
    position: absolute;
    left: 0; right: 0; bottom: 0;
    height: 67px;
    background: linear-gradient(180deg, var(--footer-mid) 0%, var(--footer-light) 35%, #ffffff 100%);
    display: flex;
    align-items: center;
    gap: 7px;
    padding-left: 18px;
  }
  .content-footer .brand-name { font-size: 17px; }
  .content-footer .brand-mark { width: 9px; height: 9px; }
</style>
</head>
<body>
  <main class="deck">
    <section class="slide slide--cover" aria-label="Cover slide">
      <div class="cover-band"></div>
      <div class="cover-brand">
        <span class="brand-mark"></span>
        <span class="brand-name">KTL Stewardship</span>
      </div>
      <p class="cover-web">www.ktlstewardship.com.au</p>
    </section>

    <section class="slide slide--content" aria-label="Content slide">
      <header class="content-header">
        <h1 class="content-title">Title 01</h1>
      </header>
      <ul class="content-body">
        <li>Click to add text</li>
      </ul>
      <footer class="content-footer">
        <span class="brand-mark"></span>
        <span class="brand-name">KTL Stewardship</span>
      </footer>
    </section>
  </main>
</body>
</html>
```